Letterhead and matching envelope design for a dental office

We need a new stationary design, letterhead and envelope #10, for a dental office in Denver area. We are called Bright Harbor Dental. We want a simple and minimalistic design but not a boring design. I wish to have one good point that makes it look professional. I have attached our logo. Feel free to use either one. I want the design for letterhead and envelope look like a "matching pair" but not look the same. The envelope doesn't have to be white and it will have an address window on bottom left.

Target Market(s)

everyone who visits dentist (adults)

Industry/Entity Type

Dental

Font styles to use
Other font styles liked:
• close to font on logo or something that matches well

Requirements
Must have
• professional
• simple, minimalistic
• unique point that stands out
Nice to have
• matching but not same design for letterhead and envelope
Should not have
• not look like all the other boring designs
• no flowery, distracting feats

```html
<!DOCTYPE html>
<html lang="en">
<head>
<meta charset="utf-8">
<title>Bright Harbor Dental – Stationery</title>
<link rel="stylesheet" href="https://fonts.googleapis.com/css2?family=Open+Sans:wght@400;600;700&display=swap">
<style>
  :root {
    --green: #3ab54a;
    --green-light: #9fd9a6;
    --leaf-tint: #e9f3e6;
    --ink: #3b3b3b;
    --ink-soft: #6a6a6a;
    --paper: #ffffff;
    --backdrop: #e6e7e9;
    --shadow: 0 6px 18px rgba(0,0,0,0.12);
  }
  * { box-sizing: border-box; margin: 0; padding: 0; }
  html, body {
    width: 1200px; height: 799px; overflow: hidden;
    background: var(--backdrop);
    font-family: "Open Sans", Arial, sans-serif;
    color: var(--ink);
  }
  .canvas { position: relative; width: 1200px; height: 799px; }

  /* Logo stand-in */
  .brand { display: flex; align-items: center; gap: 7px; }
  .brand-dot { width: 10px; height: 10px; border-radius: 50%; background: var(--green); flex: none; }
  .brand-name {
    font-weight: 600; color: var(--green); letter-spacing: 0.14em;
    text-transform: uppercase; line-height: 1.25; font-size: 12px;
  }
  .brand--light .brand-dot { background: var(--paper); }
  .brand--light .brand-name { color: var(--paper); }

  /* Letterhead */
  .letterhead {
    position: absolute; left: 40px; top: 30px; width: 523px; height: 740px;
    background: var(--paper); box-shadow: var(--shadow); overflow: hidden;
  }
  .letterhead .brand { position: absolute; top: 34px; right: 40px; }
  .contact {
    position: absolute; top: 108px; right: 40px; text-align: right;
    font-size: 9.5px; line-height: 1.55; color: var(--ink);
  }
  .contact .contact-name { color: var(--green); }
  .contact-line { display: flex; justify-content: flex-end; align-items: center; gap: 5px; }
  .contact-icon { width: 10px; height: 10px; border-radius: 50%; background: var(--green); display: inline-block; }
  .contact-rule { position: absolute; right: 0; top: 2px; width: 3px; height: 68px; background: var(--green); transform: translateX(40px); }

  .letter-body { position: absolute; top: 200px; left: 44px; width: 330px; font-size: 10px; line-height: 1.6; color: var(--ink-soft); }
  .salutation { font-weight: 700; color: var(--ink); font-size: 11px; margin-bottom: 10px; }
  .letter-body p + p { margin-top: 8px; }
  .signature { width: 120px; height: 36px; margin-top: 18px; background: linear-gradient(90deg, #d9d9d9, #efefef); border-radius: 3px; }

  .leaf-art { position: absolute; border-radius: 50% 50% 40% 40%; background: var(--leaf-tint); }
  .letterhead .leaf-art { left: 150px; bottom: 120px; width: 240px; height: 150px; }

  .wave { position: absolute; left: 0; bottom: 0; display: block; }
  .web-link {
    position: absolute; color: var(--paper); font-size: 11px; letter-spacing: 0.02em;
  }
  .letterhead .web-link { left: 30px; bottom: 78px; }

  /* Envelope front */
  .envelope {
    position: absolute; left: 610px; width: 550px; height: 240px;
    background: var(--paper); box-shadow: var(--shadow); overflow: hidden;
  }
  .envelope--front { top: 60px; }
  .envelope--front .brand { position: absolute; top: 26px; right: 30px; }
  .envelope--front .leaf-art { left: 150px; bottom: 50px; width: 220px; height: 120px; }
  .envelope--front .web-link { left: 22px; bottom: 38px; font-size: 10px; }
  .return-address {
    position: absolute; right: 30px; bottom: 24px; text-align: right;
    font-size: 10px; line-height: 1.45; color: var(--ink);
  }
  .return-address .contact-name { color: var(--green); }
  .return-rule { position: absolute; right: 0; bottom: 18px; width: 4px; height: 40px; background: var(--green); }

  /* Envelope back */
  .envelope--back { top: 360px; }
  .flap { position: absolute; left: 0; top: 0; display: block; }
  .envelope--back .brand { position: absolute; top: 58px; left: 50%; transform: translateX(-50%); }
</style>
</head>
<body>
<main class="canvas">

  <section class="letterhead" aria-label="Letterhead">
    <div class="brand">
      <span class="brand-dot"></span>
      <span class="brand-name">Bright Harbor<br>Dental</span>
    </div>

    <address class="contact">
      <div class="contact-name">Bright Harbor Dental</div>
      <div>2210 Alder Ridge Rd.</div>
      <div>Suite 40 Lakewood, CO 80215</div>
      <div class="contact-line">303-555-0142 <span class="contact-icon"></span></div>
      <div class="contact-line">info@brightharbordental.com <span class="contact-icon"></span></div>
      <span class="contact-rule"></span>
    </address>

    <div class="letter-body">
      <p class="salutation">Dear Mr. Carter,</p>
      <p>Thank you for choosing our practice for your family's dental care. This letter confirms the details of your upcoming visit and the treatment plan we discussed together during your last appointment.</p>
      <p>Please arrive ten minutes early so our team can review your records. If you need to change the time, call our front desk and we will gladly find a new slot.</p>
      <p>We look forward to seeing you soon and keeping your smile healthy.</p>
      <div class="signature" role="img" aria-label="Handwritten signature"></div>
    </div>

    <div class="leaf-art" role="img" aria-label="Faint leaf decoration"></div>

    <svg class="wave" width="523" height="160" viewBox="0 0 523 160" aria-hidden="true">
      <path d="M0 8 C150 10 330 60 523 160 L0 160 Z" fill="var(--green-light)"/>
      <path d="M0 16 C150 20 320 72 500 160 L0 160 Z" fill="var(--green)"/>
    </svg>
    <span class="web-link">www.brightharbordental.com</span>
  </section>

  <section class="envelope envelope--front" aria-label="Envelope front">
    <div class="brand">
      <span class="brand-dot"></span>
      <span class="brand-name">Bright Harbor<br>Dental</span>
    </div>
    <div class="leaf-art" role="img" aria-label="Faint leaf decoration"></div>
    <svg class="wave" width="550" height="110" viewBox="0 0 550 110" aria-hidden="true">
      <path d="M0 20 C110 14 220 40 330 110 L0 110 Z" fill="var(--green-light)"/>
      <path d="M0 28 C110 24 210 50 310 110 L0 110 Z" fill="var(--green)"/>
    </svg>
    <span class="web-link">www.brightharbordental.com</span>
    <address class="return-address">
      <div class="contact-name">Bright Harbor Dental</div>
      <div>2210 Alder Ridge Rd.</div>
      <div>Suite 40 Lakewood, CO 80215</div>
    </address>
    <span class="return-rule"></span>
  </section>

  <section class="envelope envelope--back" aria-label="Envelope back">
    <svg class="flap" width="550" height="150" viewBox="0 0 550 150" aria-hidden="true">
      <path d="M0 0 L550 0 L550 120 C550 140 535 150 510 146 C420 130 330 112 275 150 C210 120 90 60 0 40 Z" fill="var(--green)"/>
    </svg>
    <div class="brand brand--light">
      <span class="brand-dot"></span>
      <span class="brand-name">Bright Harbor<br>Dental</span>
    </div>
  </section>

</main>
</body>
</html>
```